Professional Chatterly Banner, Business Cards, Door Hang Tags, Service Flyer for Pest Control Company

There are really 4 things I need designed but Pixel Bazaar doesn't have them to package together. I am needing to get a Professional Chatterly Banner, Business Cards, Door Hang Tags, and Service Flyer for a Pest Control Company. I already have a logo that I will attach to the project along with content a for each one of these tasks. Please see document attached labeled All Design Content & Flyer Content.
Industry/Entity Type
Pest Control
Look and feel
Each slider illustrates characteristics of the customer's brand and the style your logo design should communicate.

```html
<!DOCTYPE html>
<html lang="en">
<head>
<meta charset="utf-8">
<title>Citrus Grove Pest Control – Door Hang Tags</title>
<link href="https://fonts.googleapis.com/css2?family=Oswald:wght@500;600&family=Poppins:wght@300;400&display=swap" rel="stylesheet">
<style>
  :root {
    --bg: #ebe9e6;
    --ink: #050505;
    --orange: #f26a1f;
    --white: #ffffff;
    --rule: #6a6a6a;
    --display: "Oswald", "Arial Narrow", sans-serif;
    --body: "Poppins", "Helvetica Neue", sans-serif;
  }
  * { box-sizing: border-box; margin: 0; padding: 0; }
  html, body { width: 772px; height: 1200px; overflow: hidden; background: var(--bg); }
  .sheet { position: relative; width: 772px; height: 1200px; }

  .hanger {
    position: absolute; top: 202px; width: 340px; height: 795px;
    background: var(--ink); box-shadow: 0 10px 24px rgba(0,0,0,.28);
    color: var(--white); text-align: center;
  }
  .hanger--about { left: 31px; }
  .hanger--services { left: 401px; }

  .brand { position: absolute; top: 226px; left: 0; width: 100%; color: var(--orange);
    font-family: var(--display); font-weight: 600; text-transform: uppercase; }
  .brand__name { display: block; font-size: 31px; line-height: 34px; letter-spacing: 1px; }
  .brand__line { display: block; font-size: 11px; line-height: 14px; letter-spacing: 9px; padding-left: 9px; }

  .intro { position: absolute; top: 282px; left: 35px; width: 270px;
    font-family: var(--body); font-weight: 300; font-size: 14px; line-height: 19px; letter-spacing: -.3px; }

  .motto { position: absolute; top: 389px; left: 68px; width: 206px; height: 55px;
    background: var(--white); box-shadow: 3px 3px 0 var(--orange); color: var(--ink);
    font-family: var(--display); font-style: italic; font-weight: 500; font-size: 18px; line-height: 20px;
    text-transform: uppercase; padding-top: 7px; }

  .promise { position: absolute; top: 460px; left: 45px; width: 250px; color: var(--orange);
    font-family: var(--body); font-weight: 300; font-size: 12px; line-height: 16.4px; letter-spacing: -.3px; }

  .tear-line { position: absolute; top: 577px; left: 0; width: 100%; border-top: 1px dashed var(--rule); }

  .cta { position: absolute; top: 582px; left: 0; width: 100%;
    font-family: var(--display); font-style: italic; font-weight: 500; text-transform: uppercase; }
  .cta__call { display: block; font-size: 30px; line-height: 34px; }
  .cta__quote { display: block; font-size: 19px; line-height: 22px; }
  .cta__phone { display: block; margin: 5px auto 0; width: 176px; height: 33px; background: var(--orange);
    font-size: 25px; line-height: 33px; box-shadow: 2px 2px 0 var(--white); }

  .web { position: absolute; top: 683px; left: 0; width: 100%;
    font-family: var(--body); font-weight: 300; font-size: 13px; line-height: 16px; }
  .web__globe { display: inline-block; width: 11px; height: 11px; border-radius: 50%;
    background: var(--orange); margin-right: 12px; vertical-align: -1px; }

  .offer { position: absolute; top: 711px; left: 0; width: 100%; height: 60px; background: var(--white); color: var(--ink); }
  .offer__row { display: flex; justify-content: center; align-items: center; padding-top: 5px; }
  .offer__amount { color: var(--orange); font-family: var(--display); font-style: italic; font-weight: 600;
    font-size: 38px; line-height: 40px; margin-right: 6px; }
  .offer__what { font-family: var(--display); font-style: italic; font-weight: 500; font-size: 14px;
    line-height: 14px; text-align: left; text-transform: uppercase; }
  .offer__note { font-family: var(--body); font-weight: 300; font-size: 8.5px; line-height: 10px; margin-top: -1px; }

  .services-title { position: absolute; top: 306px; left: 89px; width: 162px; height: 36px;
    background: var(--orange); box-shadow: 2px 2px 0 var(--white);
    font-family: var(--display); font-style: italic; font-weight: 600; font-size: 24px; line-height: 36px; text-transform: uppercase; }

  .services { position: absolute; top: 362px; left: 73px; width: 220px; list-style: none;
    display: grid; grid-template-columns: 116px 104px; row-gap: 15px; text-align: left; }
  .service { display: flex; align-items: center; height: 26px;
    font-family: var(--display); font-style: italic; font-weight: 500; font-size: 16px; line-height: 15px; text-transform: uppercase; }
  .service__icon { flex: none; width: 22px; height: 22px; border: 2px solid var(--orange);
    background: #3a3a3a; margin-right: 6px; }
</style>
</head>
<body>
<main class="sheet">

  <section class="hanger hanger--about">
    <div class="brand"><span class="brand__name">Citrus Grove</span><span class="brand__line">Pest Control</span></div>
    <p class="intro">We are a locally owned and operated, with 10 years of industry experience our family is committed to delivering exceptional customer service and high-quality results.</p>
    <p class="motto">We strive for excellence<br>in all that we do.</p>
    <p class="promise">We treat each and every customer like a member of our family. When you partner with us, you can enjoy hassle-free services, expert care, and peace of mind knowing you and your home are protected from pests for years to come.</p>
    <div class="tear-line"></div>
    <div class="cta"><span class="cta__call">Call Now!</span><span class="cta__quote">For a free quote</span><span class="cta__phone">(555) 014-2278</span></div>
    <p class="web"><span class="web__globe"></span>www.citrusgrovepest.com</p>
    <div class="offer">
      <div class="offer__row"><span class="offer__amount">50% OFF</span><span class="offer__what">Initial Home<br>Protection Plan</span></div>
      <p class="offer__note">New Customers Only</p>
    </div>
  </section>

  <section class="hanger hanger--services">
    <div class="brand"><span class="brand__name">Citrus Grove</span><span class="brand__line">Pest Control</span></div>
    <h2 class="services-title">Our Services</h2>
    <ul class="services">
      <li class="service"><span class="service__icon" role="img" aria-label="ant icon"></span>Ants</li>
      <li class="service"><span class="service__icon" role="img" aria-label="rat icon"></span>Rats</li>
      <li class="service"><span class="service__icon" role="img" aria-label="mosquito icon"></span>Mosquitos</li>
      <li class="service"><span class="service__icon" role="img" aria-label="mouse icon"></span>Mice</li>
      <li class="service"><span class="service__icon" role="img" aria-label="flea icon"></span>Fleas</li>
      <li class="service"><span class="service__icon" role="img" aria-label="termite icon"></span>Termites</li>
      <li class="service"><span class="service__icon" role="img" aria-label="roach icon"></span>Roaches</li>
      <li class="service"><span class="service__icon" role="img" aria-label="rodent icon"></span>Rodents</li>
      <li class="service"><span class="service__icon" role="img" aria-label="wasp icon"></span>Stinging<br>Insects</li>
      <li class="service"><span class="service__icon" role="img" aria-label="spider icon"></span>Spiders</li>
    </ul>
    <div class="tear-line"></div>
    <div class="cta"><span class="cta__call">Call Now!</span><span class="cta__quote">For a free quote</span><span class="cta__phone">(555) 014-2278</span></div>
    <p class="web"><span class="web__globe"></span>www.citrusgrovepest.com</p>
    <div class="offer">
      <div class="offer__row"><span class="offer__amount">25% OFF</span><span class="offer__what">One Time<br>Service</span></div>
      <p class="offer__note">New Customers Only</p>
    </div>
  </section>

</main>
</body>
</html>
```